Super Greens Label for Supplement Bottle

We want to design a front label for a health supplement bottle. The product is called Meadow Crunch Chews™. This will be a new product so there is no current website for the product. The focus is on supergreens that taste great and deliver support for energy, digestion, and immune defense.
We want it to be modern, vibrant and appealing.
Bottle size: standard size supplement CLEAR bottle size, with white child resistant cap and the label panel dimensions are 3” x 7”. The label should be primarily white and green, with a touch of red; (see color palettes)/it can also ONLY be white and green. See samples attached.
We are only focused on the front of the bottle design, not on the back, but leave space for the supplement panel and other text on the back.
So the text for the front of the bottle is:
RT Halvorsen's
Meadow Crunch Chews™
Super Greens Blend for:
Energy, Digestion, and Immune Support*
60 Gummies | Dietary Supplement
Raspberry Flavor Gummies
Off to side of the label:
Non-GMO
Vegan Friendly
Plant-Based
Gelatin Free
Colors
Designer to choose colors to be used in the design.
Look and feel
Each slider illustrates characteristics of the customer's brand and the style your logo design should communicate.

```html
<!DOCTYPE html>
<html lang="en">
<head>
<meta charset="utf-8">
<title>Meadow Crunch Chews – Front Label</title>
<link rel="stylesheet" href="https://fonts.googleapis.com/css2?family=Anton&display=swap">
<style>
  :root {
    --page-bg: #f4f4f4;
    --green-deep: #0f7a55;
    --green-mid: #1a9169;
    --green-light: #5fbf9c;
    --green-dark: #1d6a4c;
    --white: #ffffff;
  }
  html, body {
    margin: 0;
    width: 1200px;
    height: 960px;
    overflow: hidden;
    background: var(--page-bg);
  }
  .canvas {
    position: relative;
    width: 1200px;
    height: 960px;
  }
  .label {
    position: absolute;
    left: 250px;
    top: 70px;
    width: 700px;
    height: 820px;
    background: linear-gradient(90deg, var(--green-light) 0%, var(--green-mid) 18%, var(--green-deep) 50%, var(--green-mid) 82%, var(--green-light) 100%);
    font-family: "Anton", "Impact", sans-serif;
    color: var(--white);
    overflow: hidden;
  }
  .brand-name {
    position: absolute;
    left: 60px;
    top: 60px;
    font-size: 62px;
    line-height: 0.95;
    text-transform: uppercase;
    margin: 0;
  }
  .product-name {
    position: absolute;
    left: 56px;
    top: 210px;
    margin: 0;
    font-size: 140px;
    line-height: 0.9;
    text-transform: uppercase;
    letter-spacing: 1px;
  }
  .product-name span { display: block; }
  .product-name sup { font-size: 40px; vertical-align: top; line-height: 1; }
  .tagline {
    position: absolute;
    left: 62px;
    top: 612px;
    width: 600px;
    margin: 0;
    font-size: 28px;
    line-height: 1.1;
    text-transform: uppercase;
  }
  .count {
    position: absolute;
    left: 60px;
    top: 686px;
    font-size: 104px;
    line-height: 1;
  }
  .flavor {
    position: absolute;
    left: 200px;
    top: 702px;
    background: var(--white);
    color: var(--green-dark);
    font-size: 32px;
    line-height: 1;
    padding: 6px 12px;
    text-transform: uppercase;
  }
  .supplement-type {
    position: absolute;
    left: 212px;
    top: 756px;
    font-size: 32px;
    line-height: 1;
    text-transform: uppercase;
  }
  .badge-strip {
    position: absolute;
    right: 40px;
    top: 0;
    width: 110px;
    height: 470px;
    background: var(--white);
    border-radius: 0 0 55px 55px;
  }
  .badge-strip svg { display: block; }
</style>
</head>
<body>
<div class="canvas">
  <section class="label">
    <p class="brand-name">Your logo<br>here</p>

    <h1 class="product-name">
      <span>Meadow</span>
      <span>Crunch</span>
      <span>Chews<sup>™</sup></span>
    </h1>

    <p class="tagline">Super greens blend for energy, digestion, and immune support*</p>

    <div class="count">60</div>
    <div class="flavor">Raspberry flavor gummies</div>
    <div class="supplement-type">Dietary supplement</div>

    <div class="badge-strip" aria-label="Product attribute badges">
      <svg width="110" height="470" viewBox="0 0 110 470">
        <g fill="none" stroke="#1a9169" stroke-width="3">
          <circle class="badge" cx="55" cy="65" r="38"/>
          <circle class="badge" cx="55" cy="175" r="38"/>
          <circle class="badge" cx="55" cy="285" r="38"/>
          <circle class="badge" cx="55" cy="400" r="38"/>
        </g>
      </svg>
    </div>
  </section>
</div>
</body>
</html>
```